Business Card Re-Design/Update

We'd like to update out business cards. I've included our current "Style guide" which has the colour scheme of the organisation in it. I've also included the branding files with logos etc in them.

I've also included a copy of one of our existing cards so that you can see how ugly/dated they look. I'd like a fresh modern corporate look.

Target Market(s)

These are for our clients, potential clients, industry contacts - like all business cards

Contact Information for Business Card

Name
Position
Company Address - Level 1, 47 Fernby Street, Carlow Qld 4072
Direct Phone
mobile
Email
Website -www.korvalit.com.au
Logo

Colors

Designer to choose colors to be used in the design.

Requirements
Must have
• Main Logo
• Cards will need to be editable to be able to personalize them for each new employee.
Nice to have
• The MapOut, ShipWell, KeepSteady would be okay to have if they can be sensibly and professionally added to the look without detracting from the main imagery.
• Maybe they could go on the back of the card? will leave this to your creative discretion as to whether/where they fit.
Should not have
• Should not have decorative or script fonts

```html
<!DOCTYPE html>
<html lang="en">
<head>
<meta charset="utf-8">
<title>Korvalit Business Card</title>
<link rel="stylesheet" href="https://fonts.googleapis.com/css2?family=Arimo:wght@400;700&display=swap">
<style>
  :root {
    --stage: #3b3532;
    --card: #121212;
    --brand-red: #e3222b;
    --text-light: #e6e6e6;
    --text-grey: #5c5c5c;
    --rule: #3a3a3a;
    --ship-blue: #1e8fd6;
    --map-green: #6cb33f;
    --keep-magenta: #c5289a;
  }
  * { box-sizing: border-box; margin: 0; padding: 0; }
  html, body { width: 1200px; height: 844px; overflow: hidden; }
  body {
    background: var(--stage);
    font-family: "Arimo", Arial, sans-serif;
    position: relative;
  }
  .card {
    position: absolute;
    top: 263px;
    width: 520px;
    height: 318px;
    background: var(--card);
    box-shadow: 0 10px 30px rgba(0,0,0,.45);
  }
  .card--front { left: 50px; }
  .card--back { left: 630px; }

  /* front */
  .front-brand {
    position: absolute;
    left: 40px; top: 136px;
    display: flex; align-items: center; gap: 12px;
  }
  .brand-square {
    width: 34px; height: 34px;
    background: var(--brand-red);
  }
  .front-brand .brand-name {
    color: var(--brand-red);
    font-weight: 700;
    font-size: 30px;
    letter-spacing: .5px;
  }
  .front-divider {
    position: absolute;
    left: 250px; top: 58px;
    width: 1px; height: 210px;
    background: var(--rule);
  }
  .contact {
    position: absolute;
    left: 268px; top: 56px;
    color: var(--text-light);
    font-size: 13.5px;
    line-height: 18px;
  }
  .contact .person-name {
    color: var(--brand-red);
    font-weight: 700;
    font-size: 17px;
    letter-spacing: .5px;
    line-height: 20px;
  }
  .contact .person-role { margin-bottom: 8px; }
  .contact-list { list-style: none; margin-bottom: 10px; }
  .contact-list li { display: flex; align-items: center; gap: 8px; }
  .contact-list svg { width: 10px; height: 10px; fill: var(--brand-red); flex: none; }

  /* back */
  .back-brand {
    position: absolute;
    left: 0; right: 0; top: 88px;
    display: flex; justify-content: center; align-items: center; gap: 14px;
  }
  .back-brand .brand-square { width: 30px; height: 30px; }
  .back-brand .brand-name {
    color: var(--text-grey);
    font-size: 40px;
    font-weight: 400;
    letter-spacing: 1px;
  }
  .back-rule {
    position: absolute;
    left: 90px; right: 40px;
    height: 1px;
    background: var(--rule);
  }
  .back-rule--top { top: 60px; }
  .back-rule--bottom { top: 175px; }
  .services {
    position: absolute;
    left: 0; right: 0; top: 200px;
    display: flex; justify-content: center; gap: 22px;
    list-style: none;
  }
  .service { display: flex; align-items: center; gap: 7px; font-size: 20px; }
  .service-mark { width: 14px; height: 14px; }
  .service--ship { color: var(--ship-blue); }
  .service--ship .service-mark { background: var(--ship-blue); }
  .service--map { color: var(--map-green); }
  .service--map .service-mark { background: var(--map-green); }
  .service--keep { color: var(--keep-magenta); }
  .service--keep .service-mark { background: var(--keep-magenta); }
</style>
</head>
<body>
  <section class="card card--front" aria-label="Card front">
    <div class="front-brand">
      <span class="brand-square"></span>
      <span class="brand-name">korvalit</span>
    </div>
    <div class="front-divider"></div>
    <div class="contact">
      <p class="person-name">MARA KELLETT</p>
      <p class="person-role">Business Development Manager</p>
      <ul class="contact-list">
        <li><svg viewBox="0 0 10 10" aria-hidden="true"><path d="M1 2c0-1 1-1.5 2-1l1 2-1 1c.5 1 1.5 2 2.5 2.5l1-1 2 1c.5 1 0 2-1 2C4 8.5 1.5 6 1 2z"/></svg>+61 (0)412 550 318</li>
        <li><svg viewBox="0 0 10 10" aria-hidden="true"><path d="M2.5 0h5v10h-5zM3.5 1v7h3V1z"/></svg>+61 (0)7 3390 4126</li>
        <li><svg viewBox="0 0 10 10" aria-hidden="true"><path d="M2 0h5v3H2zM0 3h10v5H8v2H2V8H0zM3 6v3h4V6z"/></svg>+61 (0)7 3390 4127</li>
        <li><svg viewBox="0 0 10 10" aria-hidden="true"><path d="M0 2h10v6H0zM1 3l4 3 4-3z"/></svg>mkellett@korvalit.com.au</li>
        <li><svg viewBox="0 0 10 10" aria-hidden="true"><circle cx="5" cy="5" r="5"/></svg>www.korvalit.com.au</li>
      </ul>
      <p>Level 1, 47 Fernby Street</p>
      <p>Carlow Qld 4072</p>
    </div>
  </section>

  <section class="card card--back" aria-label="Card back">
    <div class="back-rule back-rule--top"></div>
    <div class="back-brand">
      <span class="brand-square"></span>
      <span class="brand-name">korvalit</span>
    </div>
    <div class="back-rule back-rule--bottom"></div>
    <ul class="services">
      <li class="service service--ship"><span class="service-mark"></span>ShipWell</li>
      <li class="service service--map"><span class="service-mark"></span>MapOut</li>
      <li class="service service--keep"><span class="service-mark"></span>KeepSteady</li>
    </ul>
  </section>
</body>
</html>
```